Corvane Paintless Dent Removal

Our company works on vehicles removing dents using a highly skilled trade which the metal is massaged out with special tools without disturbing the original paint, hence paintless dent removal. Besides keeping the paint and metal original its also very environmentally friendly since no paint or toxic fillers are used. Also we we are one of the most experienced companies in the business with 25 years

Target Market(s)

Retail Automobile consumers, Auto Dealerships and Auto Body Shops

Industry/Entity Type

Auto Repair

Contact Information for Business Card

Dale Hollister
PO Box 518 Brookmere, NY 11962
631-555-0148
corvanepdr@mailbox-example.com
website corvanepdr.example
youtube corvane paintless dent removal
25 years of experience removing Dents, Dings and Hail Damage

Font styles to use
Serif
Sans Serif

Colors

Designer to choose colors to be used in the design.

Requirements
Must have
• I do like things that are simple but classy and somewhat bold, also I like my logo so that should be somewhat important

```html
<!DOCTYPE html>
<html lang="en">
<head>
<meta charset="utf-8">
<title>Corvane Paintless Dent Removal — Business Card</title>
<link rel="stylesheet" href="https://fonts.googleapis.com/css2?family=Roboto:wght@400;700&display=swap">
<style>
  :root {
    --navy: #0f2748;
    --green: #6cbd1c;
    --paper: #f6f6f4;
    --ink: #555a60;
    --white: #ffffff;
    --gold: #c9971f;
    --gold-dark: #1c1a17;
    --backdrop: #e4e2de;
  }
  * { margin: 0; padding: 0; box-sizing: border-box; }
  html, body { width: 1200px; height: 960px; overflow: hidden; }
  body {
    position: relative;
    background: var(--backdrop);
    font-family: "Roboto", Arial, sans-serif;
  }
  .card {
    position: absolute;
    width: 600px;
    height: 344px;
    box-shadow: 0 3px 8px rgba(0,0,0,0.25);
    overflow: hidden;
  }
  .card-front { left: 314px; top: 113px; background: var(--paper); }
  .card-back  { left: 311px; top: 472px; background: var(--navy); }

  .name-band {
    position: absolute; left: 0; top: 45px; width: 600px; height: 71px;
  }
  .name-band svg { position: absolute; inset: 0; }
  .holder-name {
    position: absolute; left: 41px; top: 0; line-height: 71px;
    color: var(--white); font-weight: 700; font-size: 19px; letter-spacing: 0.3px;
    text-transform: uppercase;
  }
  .brand-front {
    position: absolute; left: 318px; top: 0; height: 71px;
    display: flex; flex-direction: column; justify-content: center; align-items: center;
    width: 236px;
    color: var(--white); font-weight: 700; text-transform: uppercase;
  }
  .brand-front .brand-word { font-size: 28px; line-height: 1; letter-spacing: 1px; }
  .brand-front .brand-sub { font-size: 11px; letter-spacing: 0.4px; margin-top: 3px; }

  .address {
    position: absolute; left: 41px; top: 191px;
    color: var(--ink); font-size: 14px; line-height: 18px;
  }
  .contact-list {
    position: absolute; left: 41px; top: 233px; list-style: none;
    color: var(--ink); font-size: 14px;
  }
  .contact-list li { display: flex; align-items: center; height: 19px; }
  .contact-list svg { width: 13px; height: 13px; margin-right: 10px; fill: var(--navy); flex: none; }

  .years-seal { position: absolute; left: 466px; top: 215px; width: 96px; height: 96px; }

  .brand-back {
    position: absolute; left: 0; top: 118px; width: 600px;
    display: flex; flex-direction: column; align-items: center;
    color: var(--white); font-weight: 700; text-transform: uppercase;
  }
  .brand-back .brand-word { font-size: 46px; line-height: 1; letter-spacing: 2px; }
  .brand-back .brand-sub { font-size: 17px; margin-top: 6px; letter-spacing: 0.5px; }
  .web-back {
    position: absolute; left: 0; top: 280px; width: 600px; text-align: center;
    color: var(--white); font-size: 14px; letter-spacing: 6px;
  }
</style>
</head>
<body>
  <section class="card card-front">
    <div class="name-band">
      <svg width="600" height="71" viewBox="0 0 600 71">
        <rect width="600" height="71" fill="var(--navy)"/>
        <polygon points="330,0 600,0 600,71 300,71" fill="var(--green)"/>
      </svg>
      <h1 class="holder-name">Dale Hollister</h1>
      <div class="brand-front">
        <span class="brand-word">Corvane</span>
        <span class="brand-sub">Paintless Dent Removal</span>
      </div>
    </div>

    <p class="address">PO Box 518<br>Brookmere, NY 11962</p>

    <ul class="contact-list">
      <li><svg viewBox="0 0 24 24"><path d="M6.6 10.8a15 15 0 0 0 6.6 6.6l2.2-2.2a1 1 0 0 1 1-.25 11.4 11.4 0 0 0 3.6.57 1 1 0 0 1 1 1V20a1 1 0 0 1-1 1A17 17 0 0 1 3 4a1 1 0 0 1 1-1h3.5a1 1 0 0 1 1 1c0 1.25.2 2.45.57 3.57a1 1 0 0 1-.25 1z"/></svg>631-555-0148</li>
      <li><svg viewBox="0 0 24 24"><path d="M2 5h20v14H2z M4 7v.5l8 5 8-5V7l-8 5z" fill-rule="evenodd"/></svg>corvanepdr@mailbox-example.com</li>
      <li><svg viewBox="0 0 24 24"><circle cx="12" cy="12" r="10"/><path d="M2 12h20M12 2c3 3 3 17 0 20M12 2c-3 3-3 17 0 20" stroke="var(--paper)" stroke-width="1.6" fill="none"/></svg>corvanepdr.example</li>
      <li><svg viewBox="0 0 24 24"><rect x="2" y="5" width="20" height="14" rx="3"/></svg>corvane paintless dent removal</li>
    </ul>

    <svg class="years-seal" viewBox="0 0 96 96" role="img" aria-label="25 years of experience seal">
      <circle cx="48" cy="48" r="47" fill="var(--gold)"/>
      <circle cx="48" cy="48" r="31" fill="var(--gold-dark)"/>
      <circle cx="48" cy="48" r="28" fill="var(--gold)"/>
      <text x="48" y="55" text-anchor="middle" font-family="Roboto, Arial, sans-serif" font-weight="700" font-size="24" fill="var(--gold-dark)">25</text>
      <text x="48" y="67" text-anchor="middle" font-family="Roboto, Arial, sans-serif" font-weight="700" font-size="8" fill="var(--gold-dark)">YEARS</text>
    </svg>
  </section>

  <section class="card card-back">
    <div class="brand-back">
      <span class="brand-word">Corvane</span>
      <span class="brand-sub">Paintless Dent Removal</span>
    </div>
    <p class="web-back">www.corvanepdr.example</p>
  </section>
</body>
</html>
```